Business Broker Graphics Package

Hi,

Seeking a smart and professional graphics package design including business card design (double-sided) and letterhead and PowerPoint slide template.

3 Deliverables:

1. Company Letterhead
2. Business Card (two sided) (will consider one sided designs)
3. PowerPoint Template. Requires cover PPT and 2nd page design.

For the prototype use this info:
Marcus Dellorane RPA
Registered Practice Adviser
5678 Harlow Rd.
Tampa, FL 77777
555.014.2273
Demo@Quillbrookpath.com
www.QuillbrookPath.com

I'll give exact information to winner to finalize later.

I've attached the logo..

Business card will be double sided and info for back of card is in attachment.

Look forward to your great ideas and concepts!

Target Market(s)

President's and business owners, CPA's and other professionals.

Industry/Entity Type

Business

Requirements
Nice to have
• Prefer horizontal card, but will consider vertical card design.

The business card should be all or primarily white. Text colors should be same as logo creative combination of black and forest green.

PowerPoint can be white background or lighter palette of colors I like gold color. I do not like darkly colored PowerPoint designs I prefer light and bright designs.

```html
<!DOCTYPE html>
<html lang="en">
<head>
<meta charset="utf-8">
<title>Quillbrook Path – Presentation Template</title>
<link rel="stylesheet" href="https://fonts.googleapis.com/css2?family=Arimo:wght@400;700&family=Cinzel:wght@600&display=swap">
<style>
  :root {
    --forest: #0b3d26;
    --ink: #1a1a1a;
    --stage: #9a9a9a;
    --mist: #e6eee7;
    --arc-grey: #bcbcbe;
    --rule-grey: #a9b3ab;
    --faint-grey: #dededc;
    --paper: #ffffff;
  }
  * { margin: 0; padding: 0; box-sizing: border-box; }
  html, body { width: 1200px; height: 640px; overflow: hidden; }
  body { background: var(--stage); position: relative; font-family: "Arimo", Arial, sans-serif; }

  .slide {
    position: absolute; width: 424px; height: 294px;
    background: var(--paper); overflow: hidden;
    box-shadow: 0 1px 2px rgba(0,0,0,.35);
  }
  .slide--cover-a { left: 163px; top: 13px; }
  .slide--cover-b { left: 163px; top: 326px; height: 296px; }
  .slide--inner-a { left: 623px; top: 13px; }
  .slide--inner-b { left: 623px; top: 328px; }
  .slide svg.backdrop { position: absolute; inset: 0; }

  .brand { text-align: center; line-height: 1; }
  .brand__name { font-family: "Arimo", Arial, sans-serif; font-weight: 700; color: var(--forest); }
  .brand__tagline { font-family: "Arimo", Arial, sans-serif; font-weight: 700; color: var(--ink); }

  .cover-brand { position: absolute; left: 0; right: 0; }
  .cover-brand .brand__name { font-size: 22px; }
  .cover-brand .brand__tagline { font-size: 7.6px; margin-top: 4px; }
  .slide--cover-a .cover-brand { top: 233px; }
  .slide--cover-b .cover-brand { top: 206px; }

  .contact-row {
    position: absolute; left: 0; right: 0; display: flex; justify-content: center; gap: 12px;
    font-size: 6.5px; color: var(--forest); align-items: center; line-height: 1;
  }
  .contact-row span { display: inline-flex; align-items: center; gap: 3px; }
  .contact-row svg { width: 6px; height: 7px; }
  .slide--cover-a .contact-row { top: 271px; }
  .slide--cover-b .contact-row { top: 274px; }

  .solutions {
    position: absolute; top: 246px; left: 0; right: 0; text-align: center; line-height: 1;
    font-family: "Cinzel", serif; font-weight: 600; font-size: 10px; color: var(--forest);
  }
  .services {
    position: absolute; top: 262px; left: 0; right: 0; display: flex; justify-content: center; gap: 5px;
    font-size: 6.2px; color: var(--forest); line-height: 1;
  }
  .services li { list-style: none; }
  .services li::before { content: "■ "; font-size: 4.5px; vertical-align: 1px; }

  .arc-services { font-family: "Arimo", Arial, sans-serif; font-weight: 700; font-size: 7px; fill: var(--ink); }

  .inner-brand { position: absolute; left: 23px; top: 39px; text-align: left; }
  .inner-brand .brand__name { font-size: 13px; }
  .inner-brand .brand__tagline { font-size: 4.8px; margin-top: 2px; }

  .footer-contact {
    position: absolute; right: 30px; bottom: 8px; font-size: 6px; color: var(--paper);
    display: flex; gap: 5px; line-height: 1;
  }
  .footer-contact .divider { border-left: 1px solid var(--paper); }
</style>
</head>
<body>

<section class="slide slide--cover-a">
  <svg class="backdrop" viewBox="0 0 424 294" width="424" height="294" aria-hidden="true">
    <defs><path id="service-arc" d="M 70 196 Q 212 128 356 196"/></defs>
    <rect width="424" height="294" fill="var(--mist)"/>
    <line x1="0" y1="61" x2="424" y2="61" stroke="var(--rule-grey)" stroke-width="2"/>
    <ellipse cx="212" cy="345" rx="304" ry="207" fill="var(--paper)"/>
    <ellipse cx="212" cy="345" rx="300" ry="203" fill="var(--arc-grey)"/>
    <ellipse cx="212" cy="362" rx="286" ry="186" fill="var(--paper)"/>
    <text class="arc-services"><textPath href="#service-arc">■ Business Sale   ■ Acquisition   ■ Exit Planning   ■ Valuation   ■ Growth Engineering</textPath></text>
  </svg>
  <div class="brand cover-brand">
    <p class="brand__name">QuillbrookPath</p>
    <p class="brand__tagline">Merger Acquisition Growth Experts</p>
  </div>
  <div class="contact-row">
    <span><svg viewBox="0 0 6 10"><rect x="0.5" y="0.5" width="5" height="9" rx="1" fill="var(--forest)"/></svg>555.014.2273</span>
    <span><svg viewBox="0 0 10 10"><circle cx="5" cy="5" r="4.3" fill="none" stroke="var(--forest)" stroke-width="1.2"/><line x1="1" y1="5" x2="9" y2="5" stroke="var(--forest)"/><ellipse cx="5" cy="5" rx="2" ry="4.3" fill="none" stroke="var(--forest)"/></svg>www.QuillbrookPath.com</span>
  </div>
</section>

<section class="slide slide--cover-b">
  <svg class="backdrop" viewBox="0 0 424 296" width="424" height="296" aria-hidden="true">
    <rect width="424" height="296" fill="var(--mist)"/>
    <line x1="0" y1="62" x2="424" y2="62" stroke="var(--rule-grey)" stroke-width="2"/>
    <ellipse cx="212" cy="350" rx="304" ry="208" fill="var(--paper)"/>
    <ellipse cx="212" cy="352" rx="298" ry="206" fill="var(--arc-grey)"/>
    <ellipse cx="212" cy="360" rx="288" ry="200" fill="var(--paper)"/>
  </svg>
  <div class="brand cover-brand">
    <p class="brand__name">QuillbrookPath</p>
    <p class="brand__tagline">Merger Acquisition Growth Experts</p>
  </div>
  <p class="solutions">Ownership Solutions</p>
  <ul class="services">
    <li>Business Sale</li><li>Acquisition</li><li>Exit Planning</li><li>Valuation</li><li>Growth Engineering</li>
  </ul>
  <div class="contact-row">
    <span><svg viewBox="0 0 6 10"><rect x="0.5" y="0.5" width="5" height="9" rx="1" fill="var(--forest)"/></svg>555.014.2273</span>
    <span><svg viewBox="0 0 10 10"><circle cx="5" cy="5" r="4.3" fill="none" stroke="var(--forest)" stroke-width="1.2"/><line x1="1" y1="5" x2="9" y2="5" stroke="var(--forest)"/><ellipse cx="5" cy="5" rx="2" ry="4.3" fill="none" stroke="var(--forest)"/></svg>www.QuillbrookPath.com</span>
  </div>
</section>

<section class="slide slide--inner-a">
  <svg class="backdrop" viewBox="0 0 424 294" width="424" height="294" aria-hidden="true">
    <line x1="0" y1="64" x2="424" y2="64" stroke="var(--faint-grey)" stroke-width="2.4"/>
    <polygon points="0,282 247,282 243,294 0,294" fill="var(--ink)"/>
    <polygon points="254,273 424,273 424,294 249,294" fill="var(--forest)"/>
  </svg>
  <div class="brand inner-brand">
    <p class="brand__name">QuillbrookPath</p>
    <p class="brand__tagline">Merger Acquisition Growth Experts</p>
  </div>
  <div class="footer-contact"><span>555.014.2273</span><span class="divider"></span><span>www.QuillbrookPath.com</span></div>
</section>

<section class="slide slide--inner-b">
  <svg class="backdrop" viewBox="0 0 424 294" width="424" height="294" aria-hidden="true">
    <line x1="0" y1="63" x2="424" y2="63" stroke="var(--faint-grey)" stroke-width="2.4"/>
    <polygon points="0,282 247,282 243,294 0,294" fill="var(--ink)"/>
    <polygon points="254,273 424,273 424,294 249,294" fill="var(--forest)"/>
  </svg>
  <div class="brand inner-brand">
    <p class="brand__name">QuillbrookPath</p>
    <p class="brand__tagline">Merger Acquisition Growth Experts</p>
  </div>
  <div class="footer-contact"><span>555.014.2273</span><span class="divider"></span><span>www.QuillbrookPath.com</span></div>
</section>

</body>
</html>
```